Design 4 pages for an event discovery website

This is a contest for the design of 4 pages for an events discovery website. The feature is part of the new sign-up process.

Please see the attached document for a full scope, mockups and the parent category icons.

Target Market(s)

18-35 Australian event goers

Industry/Entity Type

Events

Number of Pages Required

4 page

```html
<!DOCTYPE html>
<html lang="en">
<head>
<meta charset="utf-8">
<title>Eventora – Sign Up</title>
<link href="https://fonts.googleapis.com/css2?family=Raleway:wght@300;400;500&family=Open+Sans:wght@400&display=swap" rel="stylesheet">
<style>
  :root {
    --header-top: #2f82d2;
    --header-bottom: #1a52a6;
    --navy: #0c3a72;
    --heading-blue: #1d4f8c;
    --orange: #f7941d;
    --social-blue: #3a5aa6;
    --social-blue-dark: #2c4788;
    --panel: rgba(255, 255, 255, 0.86);
    --text: #333;
    --rule: #dcdcdc;
    --footer-bg: #efefef;
    --footer-text: #444;
    --icon-grey: #5a5a5a;
  }
  * { box-sizing: border-box; margin: 0; padding: 0; }
  html, body { width: 1200px; height: 570px; overflow: hidden; background: #fff; }
  .page { position: relative; width: 1200px; height: 570px; font-family: "Open Sans", sans-serif; color: var(--text); }

  .site-header { position: absolute; left: 0; top: 0; width: 1200px; height: 96px;
    background: linear-gradient(180deg, var(--header-top), var(--header-bottom)); }
  .brand { position: absolute; left: 141px; top: 21px; font-family: "Raleway", sans-serif; font-weight: 300;
    font-size: 40px; line-height: 48px; color: #fff; letter-spacing: 0.3px; white-space: nowrap; }
  .nav-link { position: absolute; left: 345px; top: 36px; font-family: "Raleway", sans-serif; font-weight: 400;
    font-size: 18px; color: #fff; white-space: nowrap; }
  .search { position: absolute; left: 688px; top: 37px; width: 197px; height: 28px; background: #fff;
    border: 2px solid #c9d6e6; border-radius: 14px; }
  .search span { position: absolute; left: 14px; top: 5px; font-size: 10.5px; color: #555; }
  .search svg { position: absolute; right: 10px; top: 6px; }
  .btn { position: absolute; top: 36px; height: 29px; border-radius: 15px; color: #fff;
    font-family: "Raleway", sans-serif; font-weight: 500; font-size: 13px; text-align: center; line-height: 29px; white-space: nowrap; }
  .btn-signup { left: 907px; width: 74px; background: var(--navy); }
  .btn-login { left: 987px; width: 74px; background: var(--orange); }

  .hero { position: absolute; left: 0; top: 96px; width: 1200px; height: 413px;
    background: linear-gradient(120deg, #7d3a6a 0%, #b94fbf 22%, #d98be0 45%, #e6a6d6 62%, #c070b8 80%, #6d3a78 100%); }

  .panel { position: absolute; background: var(--panel); }
  .signup-panel { left: 114px; top: 134px; width: 348px; height: 231px; }
  .signup-title { position: absolute; left: 28px; top: 20px; font-family: "Raleway", sans-serif; font-weight: 300;
    font-size: 38px; color: var(--heading-blue); white-space: nowrap; }
  .social-connect { position: absolute; left: 30px; top: 85px; width: 266px; height: 76px;
    background: linear-gradient(180deg, var(--social-blue), var(--social-blue-dark)); }
  .social-connect .mark { position: absolute; left: 28px; top: 26px; width: 16px; height: 16px; background: #fff; }
  .social-connect .divider { position: absolute; left: 69px; top: 0; width: 1px; height: 76px; background: rgba(255,255,255,0.3); }
  .social-connect .small { position: absolute; left: 93px; top: 14px; font-family: "Raleway", sans-serif; font-size: 14px; color: #fff; white-space: nowrap; }
  .social-connect .large { position: absolute; left: 93px; top: 30px; font-family: "Raleway", sans-serif; font-size: 29px; color: #fff; white-space: nowrap; }
  .alt-signup { position: absolute; left: 35px; top: 185px; font-size: 14.5px; color: #333; white-space: nowrap; }

  .benefits-panel { left: 545px; top: 136px; width: 509px; height: 296px; }
  .benefits-title { position: absolute; left: 35px; top: 32px; font-family: "Raleway", sans-serif; font-weight: 400;
    font-size: 22px; color: #333; white-space: nowrap; }
  .benefit-list { position: absolute; left: 35px; top: 74px; width: 462px; list-style: none; }
  .benefit-list li { position: relative; height: 31.6px; padding-left: 27px; font-size: 11.8px; line-height: 30px;
    color: #333; border-bottom: 1px solid var(--rule); white-space: nowrap; }
  .benefit-list li:last-child { border-bottom: none; }
  .benefit-list svg { position: absolute; left: 0; top: 6px; }

  .site-footer { position: absolute; left: 0; top: 509px; width: 1200px; height: 61px; background: var(--footer-bg); }
  .legal { position: absolute; left: 142px; top: 22px; font-size: 11.5px; color: var(--footer-text); white-space: nowrap; }
  .social-links { position: absolute; left: 975px; top: 21px; display: flex; gap: 5px; }
  .social-links span { width: 19px; height: 19px; border-radius: 3px; background: var(--icon-grey); }
</style>
</head>
<body>
<div class="page">
  <header class="site-header">
    <div class="brand">Eventora</div>
    <div class="nav-link">Find Events</div>
    <div class="search">
      <span>Search</span>
      <svg width="14" height="14" viewBox="0 0 14 14"><circle cx="5.8" cy="5.8" r="4.3" fill="none" stroke="#8a8a8a" stroke-width="1.8"/><line x1="9" y1="9" x2="12.8" y2="12.8" stroke="#8a8a8a" stroke-width="2" stroke-linecap="round"/></svg>
    </div>
    <div class="btn btn-signup">Sign Up</div>
    <div class="btn btn-login">Log In</div>
  </header>

  <section class="hero" role="img" aria-label="Photo of a decorated banquet hall with draped fabric, round tables and purple lighting"></section>

  <div class="panel signup-panel">
    <h1 class="signup-title">Sign Up</h1>
    <div class="social-connect">
      <span class="mark"></span>
      <span class="divider"></span>
      <span class="small">Connect with</span>
      <span class="large">Chatterly</span>
    </div>
    <p class="alt-signup">Or Click here to Sign Up without Chatterly</p>
  </div>

  <div class="panel benefits-panel">
    <h2 class="benefits-title">Feature Benefits</h2>
    <ul class="benefit-list">
      <li><svg width="18" height="18" viewBox="0 0 18 18"><circle cx="9" cy="9" r="9" fill="#f7941d"/><path d="M5 9.3l2.7 2.6L13 6.4" fill="none" stroke="#fff" stroke-width="2.2" stroke-linecap="round" stroke-linejoin="round"/></svg>Get personalised event recommendations</li>
      <li><svg width="18" height="18" viewBox="0 0 18 18"><circle cx="9" cy="9" r="9" fill="#f7941d"/><path d="M5 9.3l2.7 2.6L13 6.4" fill="none" stroke="#fff" stroke-width="2.2" stroke-linecap="round" stroke-linejoin="round"/></svg>Get notified about your favourite events - never miss out again</li>
      <li><svg width="18" height="18" viewBox="0 0 18 18"><circle cx="9" cy="9" r="9" fill="#f7941d"/><path d="M5 9.3l2.7 2.6L13 6.4" fill="none" stroke="#fff" stroke-width="2.2" stroke-linecap="round" stroke-linejoin="round"/></svg>Follow all your favourite artists, musicians, teams and players in one place</li>
      <li><svg width="18" height="18" viewBox="0 0 18 18"><circle cx="9" cy="9" r="9" fill="#f7941d"/><path d="M5 9.3l2.7 2.6L13 6.4" fill="none" stroke="#fff" stroke-width="2.2" stroke-linecap="round" stroke-linejoin="round"/></svg>Follow your favourite local venues to know everything happening there</li>
      <li><svg width="18" height="18" viewBox="0 0 18 18"><circle cx="9" cy="9" r="9" fill="#f7941d"/><path d="M5 9.3l2.7 2.6L13 6.4" fill="none" stroke="#fff" stroke-width="2.2" stroke-linecap="round" stroke-linejoin="round"/></svg>Get curated news and feature content on your favourite artists (coming soon)</li>
      <li><svg width="18" height="18" viewBox="0 0 18 18"><circle cx="9" cy="9" r="9" fill="#f7941d"/><path d="M5 9.3l2.7 2.6L13 6.4" fill="none" stroke="#fff" stroke-width="2.2" stroke-linecap="round" stroke-linejoin="round"/></svg>Invite your mates to events via Chatterly (CL sign-up only)</li>
    </ul>
  </div>

  <footer class="site-footer">
    <p class="legal">© 2015 Company Name&nbsp; All right reserved&nbsp; Term of Use</p>
    <div class="social-links"><span></span><span></span><span></span></div>
  </footer>
</div>
</body>
</html>
```